Tallreed Agency Website

We need a website design for a UK based marketing and PR agency called "Tallreed Agency". We are a small and vibrant team that looks after a mixture of clients from the luxury lifestyle and professional services sectors so the design needs to reflect this and convey: Professionalism, contemporary approach, creativity and the high end luxury and professional market we look after. Our services include marketing, PR, social media and copywriting and we look after both local and national clients. The design will need to incorporate the grey and orange brand colours (logo attached) but we are open to the use of more/different colours - with the possibility of a slight refresh on the current logo/branding. The main pages required include: Home, About Us, Services, Sectors, Case Studies and Blog.

ur existing website can be seen here - http://www.tallreed-example.co.uk

The site will need to showcase our approach, services and expertise, existing/previous clients, and provide frequently updated content via news and blog to support our marketing campaigns.

The key objectives for the site are:
- To support current sales activity by giving potential clients somewhere to visit to find out who we are, what we can do, what we have done
- To generate incoming sales leads/enquiries from companies looking for marketing and PR services
- To showcase us as a high end a professional agency with some fantastic clients and a wealth of experience

Target Market(s)

Professional services e.g. accountants, data centres etc
Luxury lifestyle e.g. wedding venue, tailor, homeware etc.
British market - mainly South East/London
Small - Medium sized businesses

Industry/Entity Type

Marketing

Font styles to use
Other font styles liked:
• Din Regular and Bold is currently used

Colors
f78f20
aaaaaa

Requirements
Must have
• Must Have:
- The main menu items are likely to be:
- Services
- Sectors
- About us
- Case Studies
- Blog
- Contact us

Some of these items may have a sub-menu, e.g. About us is likely to have "Company", "Team", and "Careers" below it and "Services" will have "marketing", "PR", "Copywriting", "Social media". Sectors will have "Professional", "Luxury", "Lifestyle"

Key must-have elements of the homepage include:
- Social media icons (twitter, linkedin, facebook, google+)
- Contact details (i.e. phone number and email/link)
- "We have worked with..." - this is likely to be icons for logos of previous and current clients
- "Sign up to newsletter"
- "Latest news"

Footer navigation must allow for the usual suspects (sitemap, t's & c's, privacy policy, company registration details)

Some kind of call-to-action boxes/areas/links to provide us with ways to link out to any specific micro-sites or pages within the site (e.g. to highlight some of our specific case studies, services etc).

To confirm, we are looking for the following page types/templates:
1) Home page
2) Inside/content page (can be used for services, about us etc)
3) Article page (for blog/news articles etc)
4) Case studies (an image led pad to showcase campaigns we have worked on)
4) Contact page
Nice to have
• - If web fonts are needed for the design, then please note we have an existing web fonts account with typevault-example.com and so can use any of the web fonts available there.
Should not have
• We do not want to use a one page-scroll down website

```html
<!DOCTYPE html>
<html lang="en">
<head>
<meta charset="utf-8">
<title>Tallreed Agency – Marketing &amp; PR</title>
<link rel="stylesheet" href="https://fonts.googleapis.com/css2?family=Barlow:ital,wght@0,400;0,500;0,600;1,400&family=Roboto+Condensed:wght@400&display=swap">
<style>
:root{
  --orange:#f28a1f;
  --orange-dark:#d8701a;
  --grey:#aaaaaa;
  --text:#4a4a4a;
  --muted:#666;
  --line:#dddddd;
  --white:#ffffff;
}
*{margin:0;padding:0;box-sizing:border-box}
html,body{width:1077px;height:1200px;overflow:hidden;background:var(--white)}
body{position:relative;font-family:"Barlow",sans-serif;color:var(--text)}
.abs{position:absolute}

/* nav */
.main-nav{left:0;top:0;width:1077px;height:39px;background:var(--orange)}
.main-nav ul{list-style:none;position:absolute;left:162px;top:0;display:flex;height:39px}
.main-nav li{height:39px;line-height:41px;font-size:10px;font-weight:500;letter-spacing:.6px;color:var(--white);text-transform:uppercase;padding:0 31px}
.main-nav li.active{background:var(--orange-dark);padding:0 34px}

/* header */
.brand{left:162px;top:58px;font-size:24px;color:var(--orange);font-weight:400;line-height:1}
.follow{left:418px;top:76px;font-size:8px;color:var(--orange);font-weight:500;display:flex;align-items:center;gap:4px}
.follow svg{margin-left:2px}
.divider-v{width:1px;background:var(--line)}
.getin{right:311px;top:57px;text-align:right}
.getin h3{font-size:12px;color:var(--orange);font-weight:500}
.getin p{font-size:8.5px;line-height:15px;color:var(--text);margin-top:4px}
.contact{left:800px;top:64px;font-size:9px;line-height:18px}
.contact b{color:var(--orange);font-weight:500}
.header-rule{left:0;top:116px;width:1077px;height:1px;background:#ececec}

/* hero */
.hero{left:162px;top:138px;width:754px;height:312px;background:linear-gradient(90deg,#ffffff 0%,#cfe9f7 18%,#6fb8e2 40%,#2d7db3 62%,#123e64 82%,#0b2642 100%)}
.hero-shadow{left:172px;top:450px;width:734px;height:14px;background:radial-gradient(ellipse at top,rgba(0,0,0,.28),rgba(0,0,0,0) 70%)}
.hero h1{left:187px;top:310px;font-family:"Roboto Condensed",sans-serif;font-weight:400;font-size:20px;line-height:28px;color:#3a3a3a}
.hero h1 span{font-size:22px}
.dots{left:854px;top:427px;display:flex;gap:4px}
.dots i{width:8px;height:8px;background:#b9cfe0;display:block}
.dots i.on{background:var(--orange)}

/* intro */
.intro{left:162px;top:494px;width:765px;font-size:8.6px;line-height:17.6px;color:var(--text)}

/* services */
.service{top:567px;width:171px}
.service .thumb{width:171px;height:111px}
.service h4{font-size:13px;font-weight:400;color:var(--orange);margin-top:9px}
.service p{font-size:8.6px;font-style:italic;line-height:15px;margin-top:5px;color:var(--text)}

.section-title{font-size:13px;font-weight:400;color:var(--orange);text-transform:uppercase}
.pager{display:flex;gap:6px}

/* clients */
.client{top:798px;width:138px;height:82px;border:1px solid #d6d6d6;display:flex;align-items:center;justify-content:center;text-align:center;font-size:12px;color:#666}

/* news */
.news{top:945px;width:215px}
.news h5{font-size:10.5px;font-weight:500;color:#222}
.news .meta{font-size:7.5px;font-style:italic;color:var(--orange);margin-top:6px}
.news .thumb{position:absolute;left:0;top:42px;width:99px;height:62px}
.news .excerpt{position:absolute;left:114px;top:42px;font-size:8px;line-height:15.5px;width:110px}
.btn{background:var(--orange);color:var(--white);font-size:8px;text-transform:uppercase;height:17px;line-height:17px;text-align:center;font-weight:500}
.news .btn{position:absolute;left:145px;top:114px;width:67px}

/* newsletter */
.newsletter{left:691px;top:915px;width:225px;height:151px;border:1px solid #d6d6d6}
.newsletter h4{position:absolute;left:16px;top:13px;font-size:13px;font-weight:400;color:var(--orange)}
.newsletter p{position:absolute;left:16px;top:42px;font-size:6.8px;color:#333}
.field{position:absolute;left:16px;width:191px;height:20px;border:1px solid #cfcfcf;font-size:6.8px;line-height:18px;padding-left:10px;color:#333}
.newsletter .btn{position:absolute;left:146px;top:121px;width:60px}

/* footer */
.footer-rule{left:162px;top:1109px;width:754px;height:2px;background:#dcdcdc}
.footer-links{left:165px;top:1132px;font-size:7px;color:#333;display:flex;gap:16px}
.copyright{left:164px;top:1152px;font-size:7px;color:#333}
.reg{right:290px;top:1133px;text-align:right;font-size:6.8px;line-height:16px;color:#333}
.footer-brand{left:808px;top:1128px;font-size:20px;color:var(--orange);line-height:1}
</style>
</head>
<body>

<nav class="abs main-nav">
  <ul>
    <li class="active">Home</li>
    <li>About Us</li>
    <li>Services</li>
    <li>Sectors</li>
    <li>Case Studies</li>
    <li>Blog</li>
    <li>Contact Us</li>
  </ul>
</nav>

<header>
  <div class="abs brand">Tallreed Agency</div>
  <div class="abs follow">FOLLOW US :
    <svg width="80" height="19" viewBox="0 0 80 19" aria-label="Social links">
      <circle cx="9.5" cy="9.5" r="9" fill="#d4d4d4"/>
      <circle cx="31" cy="9.5" r="9" fill="#d4d4d4"/>
      <circle cx="52.5" cy="9.5" r="9" fill="#d4d4d4"/>
      <circle cx="74" cy="9.5" r="5.5" fill="#d4d4d4"/>
    </svg>
  </div>
  <div class="abs divider-v" style="left:572px;top:58px;height:45px"></div>
  <div class="abs getin">
    <h3>Get in touch...</h3>
    <p>Call us today to find out how we can help you<br>with your marketing and PR requirements :</p>
  </div>
  <div class="abs divider-v" style="left:783px;top:58px;height:45px"></div>
  <div class="abs contact">
    <div><b>T :</b> 01632 960 418</div>
    <div><b>E :</b> hello@tallreed-example.co.uk</div>
  </div>
  <div class="abs header-rule"></div>
</header>

<section>
  <div class="abs hero" role="img" aria-label="Hand touching a glowing network of connected people icons, businessman in background"></div>
  <h1 class="abs hero" style="background:none;width:auto;height:auto;left:187px;top:310px">A brighter approach<br><span>to your Marketing &amp; PR</span></h1>
  <div class="abs dots"><i class="on"></i><i></i><i></i><i></i></div>
  <div class="abs hero-shadow"></div>
</section>

<p class="abs intro">At Tallreed Agency we have a strong background in providing marketing and PR services to clients across a broad range of sectors, both locally and international.<br>Whatever you need; from on-going social media support, regular blogging and SEO copywriting to creative PR and marketing campaigns, we deliver a cost-effective and friendly service to boost your brand and business.</p>

<section>
  <article class="abs service" style="left:162px">
    <div class="thumb" role="img" aria-label="Street signs reading marketing and strategy against a blue sky" style="background:linear-gradient(180deg,#3f8fd0,#9fc8ea 70%,#e8f1f8)"></div>
    <h4>Marketing</h4>
    <p>Whether seeking to build a new brand or refresh an existing identity for your business</p>
  </article>
  <article class="abs service" style="left:358px">
    <div class="thumb" role="img" aria-label="Hand drawing a network of connected people" style="background:linear-gradient(90deg,#ffffff,#eef4f8 55%,#c9dbe8)"></div>
    <h4>PR Services</h4>
    <p>Whether seeking to build a new brand or refresh an existing identity for your business</p>
  </article>
  <article class="abs service" style="left:553px">
    <div class="thumb" role="img" aria-label="Finger touching a web of social media icons" style="background:linear-gradient(135deg,#7fbde8,#2f86c9 55%,#9ccbec)"></div>
    <h4>Social Media</h4>
    <p>Whether seeking to build a new brand or refresh an existing identity for your business</p>
  </article>
  <article class="abs service" style="left:745px">
    <div class="thumb" role="img" aria-label="Close-up of printed text about copyright" style="background:linear-gradient(180deg,#f4f4f4,#d9d9d9 50%,#bdbdbd)"></div>
    <h4>Copywriting</h4>
    <p>Whether seeking to build a new brand or refresh an existing identity for your business</p>
  </article>
</section>

<section>
  <h2 class="abs section-title" style="left:162px;top:765px">We have worked with</h2>
  <svg class="abs" style="left:894px;top:769px" width="22" height="9" viewBox="0 0 22 9" aria-label="Previous and next">
    <path d="M5 1 L1.5 4.5 L5 8" fill="none" stroke="#777" stroke-width="1.2"/>
    <path d="M16 1 L19.5 4.5 L16 8" fill="none" stroke="#777" stroke-width="1.2"/>
  </svg>
  <div class="abs client" style="left:162px">Eastmere Barns</div>
  <div class="abs client" style="left:316px">Iron Lilies</div>
  <div class="abs client" style="left:470px">Chalk Hills Park Trust</div>
  <div class="abs client" style="left:624px">The Fine Goods Market</div>
  <div class="abs client" style="left:778px">Howard Lennox</div>
</section>

<section>
  <h2 class="abs section-title" style="left:162px;top:913px">Latest News</h2>
  <svg class="abs" style="left:641px;top:917px" width="22" height="9" viewBox="0 0 22 9" aria-label="Previous and next">
    <path d="M5 1 L1.5 4.5 L5 8" fill="none" stroke="#777" stroke-width="1.2"/>
    <path d="M16 1 L19.5 4.5 L16 8" fill="none" stroke="#777" stroke-width="1.2"/>
  </svg>
  <article class="abs news" style="left:163px">
    <h5>Eastmere Barns host inaugural wedding fair</h5>
    <div class="meta">Posted Wednesday 23 October 2013 by Clara Whitby</div>
    <div class="thumb" role="img" aria-label="Wedding rings resting on a rose" style="background:radial-gradient(circle at 40% 50%,#b08a6a,#d8cbbd 60%,#efe8e0)"></div>
    <p class="excerpt">On Sunday 22nd September our client Eastmere Barns Wedding Venue held their very first Wedding...</p>
    <div class="btn">Read More</div>
  </article>
  <div class="abs divider-v" style="left:404px;top:955px;height:100px"></div>
  <article class="abs news" style="left:440px">
    <h5>KTRM Computer Services choose Tallreed</h5>
    <div class="meta">Posted Wednesday 23 October 2013 by Clara Whitby</div>
    <div class="thumb" style="border:1px solid #d6d6d6;display:flex;align-items:center;justify-content:center;font-size:10px;color:#555">KTRM</div>
    <p class="excerpt">On Sunday 22nd September our client Eastmere Barns Wedding Venue held their very first Wedding...</p>
    <div class="btn">Read More</div>
  </article>

  <form class="abs newsletter">
    <h4>NEWSLETTER SIGNUP</h4>
    <p>GET OUR RECENT UPDATES THROUGH YOUR EMAIL ID :</p>
    <div class="field" style="top:60px">NAME :</div>
    <div class="field" style="top:91px">EMAIL :</div>
    <div class="btn">Submit</div>
  </form>
</section>

<footer>
  <div class="abs footer-rule"></div>
  <div class="abs footer-links"><span>SITEMAP</span><span>|</span><span>TERMS &amp; CONDITIONS</span><span>|</span><span>PRIVACY POLICY</span></div>
  <div class="abs copyright">COPYRIGHT © 2013 TALLREED LTD. ALL RIGHTS RESERVED</div>
  <div class="abs reg">TALLREED LTD, REGISTERED IN ENGLAND. REGISTRATION NUMBER: 7421583.<br>REGISTERED OFFICE: LOWER GROUND FLOOR, 12 HARBOUR ROW, WESTBURY, WEST SUSSEX, PO20 4XZ</div>
  <div class="abs divider-v" style="left:802px;top:1126px;height:38px;background:#bbb"></div>
  <div class="abs footer-brand">Tallreed<br>Agency</div>
</footer>

</body>
</html>
```